RW Framewell Inc Business cards

We need business cards using our existing logo but slightly modified. Right now the logo says RW Loadbearing Masonry. We want to keep the RW part of the design, but replace the Structural Concrete portion with "FRAMEWELL". Please see the attached file.
Ideally this would be a blank template so we can add Different Names, titles, and phone numbers later.
On the one side we want only the logo and on the other side the detail. I'm attaching an example for you to see.
Please reach out with any other questions. Our address and other details will be given out once we find a design we like.

Target Market(s)

Construction Industry

```html
<!DOCTYPE html>
<html lang="en">
<head>
<meta charset="utf-8">
<title>RW Framewell Inc Business Cards</title>
<link rel="stylesheet" href="https://fonts.googleapis.com/css2?family=Montserrat:wght@600&family=Roboto:wght@400;500&display=swap">
<style>
  :root {
    --backdrop: #3b3c3e;
    --card: #1d1e20;
    --brand-blue: #2f63a8;
    --brand-blue-deep: #2a5794;
    --stripe-grey: #6e6f72;
    --text-light: #f2f2f2;
  }
  * { margin: 0; padding: 0; box-sizing: border-box; }
  html, body {
    width: 799px; height: 1200px; overflow: hidden;
    background: var(--backdrop);
  }
  .sheet { position: relative; width: 799px; height: 1200px; }
  .card {
    position: absolute; left: 80px;
    width: 640px; height: 366px;
    background: var(--card);
    border-radius: 4px;
    overflow: hidden;
    box-shadow: 0 10px 24px rgba(0,0,0,0.45);
  }
  .card--front { top: 150px; }
  .card--back { top: 690px; }

  .wordmark {
    position: absolute;
    display: flex; align-items: center; gap: 14px;
    font-family: "Montserrat", sans-serif;
    font-weight: 600;
    color: var(--text-light);
    letter-spacing: 0.14em;
    white-space: nowrap;
  }
  .wordmark__mark { width: 22px; height: 22px; background: var(--brand-blue); }
  .card--front .wordmark {
    left: 50%; top: 50%;
    transform: translate(-50%, -50%);
    font-size: 40px;
  }
  .card--back .wordmark { left: 34px; top: 70px; font-size: 28px; }
  .card--back .wordmark__mark { width: 18px; height: 18px; }

  .accent-band {
    position: absolute; left: 0; right: 0; bottom: 0;
    height: 136px;
    background: linear-gradient(180deg, var(--brand-blue) 0%, var(--brand-blue-deep) 100%);
    border-top: 6px solid var(--stripe-grey);
  }

  .identity {
    position: absolute; right: 34px; top: 50px;
    text-align: right;
    font-family: "Roboto", sans-serif;
    color: var(--text-light);
  }
  .identity__name {
    font-size: 21px; font-weight: 500;
    color: var(--brand-blue);
    letter-spacing: 0.02em;
  }
  .identity__title { font-size: 14px; margin-top: 2px; }
  .identity__address { font-size: 14px; line-height: 1.45; margin-top: 12px; }

  .contacts {
    position: absolute; right: 34px; bottom: 26px;
    list-style: none;
    font-family: "Roboto", sans-serif;
    font-size: 15px;
    color: var(--text-light);
  }
  .contacts__item {
    display: flex; align-items: center; justify-content: flex-end;
    gap: 10px; line-height: 1.5;
  }
  .contacts__icon { width: 14px; height: 14px; flex: none; }
</style>
</head>
<body>
<main class="sheet">

  <section class="card card--front" aria-label="Business card front">
    <div class="wordmark"><span class="wordmark__mark"></span>RW FRAMEWELL</div>
  </section>

  <section class="card card--back" aria-label="Business card back">
    <div class="accent-band" role="img" aria-label="Decorative blue and grey swoosh band"></div>

    <div class="wordmark"><span class="wordmark__mark"></span>RW FRAMEWELL</div>

    <div class="identity">
      <p class="identity__name">Alex RW Turner</p>
      <p class="identity__title">Managing Director</p>
      <p class="identity__address">58 Harbor Lane, Millbrook,<br>Oregon, US 97001</p>
    </div>

    <ul class="contacts">
      <li class="contacts__item">555-014-2236
        <svg class="contacts__icon" viewBox="0 0 16 16" aria-hidden="true"><path fill="#fff" d="M3.5 1.5 6 4 4.8 5.6c.8 1.9 3.7 4.8 5.6 5.6L12 10l2.5 2.5-1.6 2C8 14.3 1.7 8 1.5 3.1z"/></svg>
      </li>
      <li class="contacts__item">framewell-example.com
        <svg class="contacts__icon" viewBox="0 0 16 16" aria-hidden="true"><rect x="1" y="3" width="14" height="10" fill="#fff"/><path d="M1.5 3.5 8 9l6.5-5.5" stroke="var(--brand-blue)" stroke-width="1.3" fill="none"/></svg>
      </li>
      <li class="contacts__item">alex@framewell-example.com
        <svg class="contacts__icon" viewBox="0 0 16 16" aria-hidden="true"><circle cx="8" cy="8" r="6.5" fill="none" stroke="#fff" stroke-width="1.3"/><ellipse cx="8" cy="8" rx="2.8" ry="6.5" fill="none" stroke="#fff" stroke-width="1.1"/><path d="M1.5 8h13" stroke="#fff" stroke-width="1.1"/></svg>
      </li>
    </ul>
  </section>

</main>
</body>
</html>
```